Website Design - TallyPorchHelpers.net

PLEASE CHECK WORD DOCUMENT ATTACHED FOR WEBSITE FLOW.

Target Market(s)

REAL ESTATE AGENTS ARE THE TARGET MARKET

Industry/Entity Type

Real Estate

Coding

Coded - Design and coding required

Number of Pages Required

4 page

Colors

Designer to choose colors to be used in the design.

Requirements
Must have
• WE LIKE RED LOGO ATTACHED
Nice to have
• PLEASE CHECK WORD DOCUMENT ATTACHED FOR WEBSITE FLOW.
Should not have

```html
<!DOCTYPE html>
<html lang="en">
<head>
<meta charset="utf-8">
<title>TallyPorchHelpers.net</title>
<link href="https://fonts.googleapis.com/css2?family=Lato:wght@400;700;900&family=Open+Sans:wght@400;600;700&family=Roboto:wght@400;500&display=swap" rel="stylesheet">
<style>
:root{
  --red:#e0101c;
  --indigo:#27238f;
  --navy:#2b2a93;
  --ink:#222;
  --grey:#555;
  --light:#f2f2f2;
  --dark:#2f2f2f;
  --footer:#262626;
  --line:#d9d9d9;
}
*{box-sizing:border-box;margin:0;padding:0}
html,body{width:1200px;height:4545px;overflow:hidden;background:#fff}
body{font-family:"Open Sans",sans-serif;color:var(--ink);position:relative}
.block{position:absolute;left:0;width:1200px}
.abs{position:absolute}

/* header */
.site-header{top:0;height:120px;background:#fff}
.brand{left:75px;top:22px;display:flex;align-items:center;gap:10px}
.brand-mark{width:26px;height:26px;background:var(--red);border-radius:50%}
.brand-name{font-family:"Lato",sans-serif;font-weight:900;font-size:22px;color:var(--red)}
.header-signup{left:568px;top:44px;display:flex}
.header-signup .email{width:235px;height:42px;border:1px solid var(--line);border-radius:21px 0 0 21px;font-size:13px;padding:12px 18px;color:#444}
.header-signup .btn{width:102px;height:42px;background:var(--indigo);color:#fff;border-radius:0 21px 21px 0;font-family:"Lato",sans-serif;font-weight:700;font-size:15px;display:flex;align-items:center;justify-content:center}
.call{left:930px;top:36px;display:flex;align-items:center;gap:18px}
.call-icon{width:42px;height:42px;border-radius:50%;background:var(--red);display:flex;align-items:center;justify-content:center}
.call small{display:block;font-family:"Lato",sans-serif;font-weight:700;font-size:13px;color:var(--red)}
.call strong{display:block;font-family:"Lato",sans-serif;font-weight:700;font-size:20px;color:var(--red);margin-top:4px}

.main-nav{top:120px;height:58px;background:var(--navy);display:flex;align-items:center;padding-left:78px;gap:44px}
.main-nav a{color:#fff;text-decoration:none;font-family:"Lato",sans-serif;font-weight:700;font-size:14px}

/* hero */
.hero{top:178px;height:487px;background:linear-gradient(180deg,#5d6a7a 0%,#3d4652 45%,#4b5a3c 80%,#3c4a30 100%)}
.hero-title{left:145px;top:130px;width:910px;font-family:"Lato",sans-serif;font-weight:900;font-size:32px;line-height:42px;color:#fff;text-align:center}
.hero-arrow{top:160px}
.choice{top:600px;width:330px;height:125px;background:linear-gradient(135deg,var(--red) 0%,#8a1a54 55%,var(--indigo) 100%);border-radius:4px;color:#fff;font-family:"Lato",sans-serif;font-weight:700;font-size:15px;text-align:center;padding-top:28px}
.choice svg{display:block;margin:0 auto 22px}

/* how it works */
.section-title{font-family:"Lato",sans-serif;font-weight:900;font-size:30px;color:var(--indigo);text-align:center;width:1200px;left:0}
.step-num{width:116px;height:116px;border-radius:50%;background:var(--indigo);color:#fff;font-family:"Lato",sans-serif;font-size:46px;display:flex;align-items:center;justify-content:center;top:862px}
.step-text{top:995px;width:260px;font-size:13px;line-height:21px;color:#333;text-align:center}
.step-arrow{top:905px}

/* packages */
.packages{top:1145px;height:600px;background:linear-gradient(180deg,#fff 0%,#eeeeee 40%,#e8e8e8 100%)}
.packages .section-title{top:58px;color:var(--ink)}
.pkg{top:125px;width:203px;height:440px;background:#fff;border:1px solid #d5d5d5;border-radius:6px;text-align:center;padding-top:18px}
.pkg .badge{width:96px;height:96px;margin:0 auto;border-radius:50%;background:var(--indigo);color:#fff;display:flex;flex-direction:column;align-items:center;justify-content:center;font-family:"Lato",sans-serif;font-weight:700}
.pkg .badge span{font-size:17px}
.pkg .badge b{font-size:29px;margin-top:2px}
.pkg p{font-size:13px;line-height:20px;color:#333;width:160px;margin:14px auto 0}
.pkg .buy{width:110px;height:34px;border-radius:17px;background:var(--indigo);color:#fff;font-family:"Lato",sans-serif;font-weight:700;font-size:13px;display:flex;align-items:center;justify-content:center;margin:26px auto 0}
.pkg .note{font-size:9px;font-weight:700;line-height:13px;margin-top:16px;width:180px}
.pkg.featured{background:linear-gradient(180deg,var(--red) 0%,#901c55 50%,var(--indigo) 100%);border-color:transparent;color:#fff}
.pkg.featured p{color:#fff}
.pkg.featured .badge{background:#fff;color:var(--indigo)}
.pkg.featured .buy{background:#fff;color:var(--indigo)}
.pkg .flag{position:absolute;top:72px;left:0;width:203px;height:16px;background:var(--red);color:#fff;font-size:9px;font-weight:700;line-height:16px}

/* services */
.services{top:1745px;height:395px;background:var(--dark);color:#fff}
.services h2{position:absolute;top:52px;left:230px;width:740px;text-align:center;font-family:"Lato",sans-serif;font-weight:900;font-size:29px;line-height:38px}
.service{top:162px;width:240px;text-align:center}
.service svg{display:block;margin:0 auto}
.service h3{font-family:"Lato",sans-serif;font-weight:700;font-size:19px;margin-top:16px}
.service p{font-size:13px;line-height:20px;margin-top:12px}

/* service area */
.area-title{top:2185px}
.area{top:2262px;height:573px}
.area h2{position:absolute;left:75px;top:70px;width:330px;font-family:"Lato",sans-serif;font-weight:900;font-size:29px;line-height:36px;color:var(--ink)}
.area .loc{position:absolute;left:75px;top:210px;width:330px;height:40px;border:1px solid var(--line);font-size:13px;padding:11px 12px;color:#444}
.area .map{position:absolute;left:448px;top:0;width:752px;height:573px;background:linear-gradient(135deg,#c8dff0 0%,#e8ecd9 35%,#f1eedf 60%,#dfe9cf 100%)}

/* faq */
.faq-title{top:2873px;color:var(--ink)}
.faq-item{left:75px;width:1050px;border:1px solid #d0d0d0;font-family:"Roboto",sans-serif;background:#fff}
.faq-item .q{height:58px;display:flex;align-items:center;justify-content:space-between;padding:0 30px;font-size:20px;color:#333;text-transform:uppercase}
.faq-item .a{background:#ececec;padding:16px 20px;font-size:15px;line-height:22px;color:#444;height:126px}

/* testimonial */
.testimonial{top:3425px;height:460px;background:var(--red)}
.testimonial h2{position:absolute;top:42px;width:1200px;text-align:center;font-family:"Lato",sans-serif;font-weight:900;font-size:30px;color:#fff}
.quote-card{position:absolute;left:205px;top:110px;width:790px;height:285px;background:#fff;text-align:center}
.avatar{width:78px;height:78px;border-radius:50%;background:linear-gradient(135deg,#c9a690,#7c6658);margin:52px auto 0;border:3px solid #eee}
.quote-card p{font-family:"Roboto",sans-serif;font-size:15px;line-height:22px;color:#444;width:560px;margin:22px auto 0}
.quote-card b{display:block;font-family:"Roboto",sans-serif;font-weight:500;font-size:17px;margin-top:4px}
.quote-card small{display:block;font-size:12px;color:#444;margin-top:4px}
.dots{position:absolute;top:425px;left:0;width:1200px;display:flex;justify-content:center;gap:12px}
.dots i{width:10px;height:10px;border-radius:50%;background:#fff}

/* contact */
.contact-title{top:3942px;color:var(--ink)}
.field{position:absolute;background:#efefef;font-family:"Lato",sans-serif;font-weight:700;font-size:12px;color:#333;padding:12px 22px}
.submit{left:528px;top:4243px;width:144px;height:36px;border-radius:18px;background:linear-gradient(90deg,var(--red),var(--indigo));color:#fff;font-family:"Lato",sans-serif;font-weight:700;font-size:13px;display:flex;align-items:center;justify-content:center}
.newsletter{left:1152px;top:3955px;width:48px;height:325px;background:var(--red);border-radius:14px 0 0 14px;border:3px solid var(--indigo);border-right:none;display:flex;align-items:center;justify-content:center}
.newsletter span{transform:rotate(-90deg);white-space:nowrap;color:#fff;font-family:"Lato",sans-serif;font-weight:700;font-size:20px}

/* footer */
.site-footer{top:4355px;height:190px;background:var(--footer);color:#fff}
.site-footer .brand{left:92px;top:30px}
.site-footer .tag{position:absolute;left:92px;top:105px;width:480px;font-size:11px;font-weight:700;line-height:19px}
.foot-nav{position:absolute;right:75px;top:50px;display:flex;gap:44px;font-family:"Lato",sans-serif;font-weight:700;font-size:13px}
.copy{position:absolute;right:75px;top:82px;font-size:12px;color:#ccc}
.social{position:absolute;right:75px;top:118px;display:flex;gap:18px}
.social i{width:18px;height:18px;border-radius:50%;background:#fff}
</style>
</head>
<body>

<header class="block site-header">
  <div class="abs brand"><span class="brand-mark"></span><span class="brand-name">TallyPorchHelpers.net</span></div>
  <div class="abs header-signup"><div class="email">Enter Email Address</div><div class="btn">SIGN UP</div></div>
  <div class="abs call">
    <span class="call-icon"><svg width="20" height="20" viewBox="0 0 24 24"><path fill="#fff" d="M6.6 10.8a15.1 15.1 0 006.6 6.6l2.2-2.2c.3-.3.7-.4 1-.2 1.1.4 2.3.6 3.6.6.6 0 1 .4 1 1V20c0 .6-.4 1-1 1A17 17 0 013 4c0-.6.4-1 1-1h3.5c.6 0 1 .4 1 1 0 1.3.2 2.5.6 3.6.1.3 0 .7-.2 1z"/></svg></span>
    <div><small>CALL OR TEXT US</small><strong>1-555-014-2290</strong></div>
  </div>
</header>

<nav class="block main-nav">
  <a href="#">HOW IT WORKS</a><a href="#">SERVICE AREA</a><a href="#">PRICING</a><a href="#">ABOUT US</a><a href="#">FAQ</a>
</nav>

<section class="block hero" role="img" aria-label="Photo of a two-storey suburban house with trees at dusk">
  <h1 class="abs hero-title">Helping agents save time and money. We place signs and boost foot traffic to your open houses using proven marketing techniques.</h1>
  <svg class="abs hero-arrow" style="left:62px" width="20" height="36" viewBox="0 0 20 36"><path d="M16 4L4 18l12 14" stroke="#fff" stroke-width="4" fill="none"/></svg>
  <svg class="abs hero-arrow" style="left:1118px" width="20" height="36" viewBox="0 0 20 36"><path d="M4 4l12 14L4 32" stroke="#fff" stroke-width="4" fill="none"/></svg>
</section>

<div class="abs choice" style="left:75px">
  <svg width="28" height="28" viewBox="0 0 24 24"><circle cx="12" cy="7" r="5" fill="#fff"/><path d="M3 23c0-6 4-9 9-9s9 3 9 9z" fill="#fff"/></svg>
  I'M A FULL ON BROKERAGE</div>
<div class="abs choice" style="left:435px">
  <svg width="34" height="28" viewBox="0 0 30 24"><circle cx="15" cy="6" r="4.5" fill="#fff"/><circle cx="6" cy="8" r="3.5" fill="#fff"/><circle cx="24" cy="8" r="3.5" fill="#fff"/><path d="M7 22c0-5 3.5-8 8-8s8 3 8 8z" fill="#fff"/><path d="M0 20c0-4 2.5-6.5 6-6.5 1 0 2 .2 2.8.6A9 9 0 006 20zM30 20c0-4-2.5-6.5-6-6.5-1 0-2 .2-2.8.6A9 9 0 0124 20z" fill="#fff"/></svg>
  I'M AN IND. BROKER WITH A TEAM</div>
<div class="abs choice" style="left:795px">
  <svg width="28" height="28" viewBox="0 0 24 24"><rect x="2" y="2" width="20" height="20" rx="3" fill="#fff"/><path d="M7 17l1-4 7-7 3 3-7 7z" fill="#8a1a54"/></svg>
  I NEED SIGN PLACEMENT ASAP</div>

<h2 class="abs section-title" style="top:790px">HOW IT WORKS</h2>
<div class="abs step-num" style="left:182px">01</div>
<div class="abs step-num" style="left:542px">02</div>
<div class="abs step-num" style="left:902px">03</div>
<svg class="abs step-arrow" style="left:360px" width="125" height="30" viewBox="0 0 125 30"><path d="M0 15h120M106 4l14 11-14 11" stroke="#9b9bd0" stroke-width="2.5" fill="none"/></svg>
<svg class="abs step-arrow" style="left:720px" width="125" height="30" viewBox="0 0 125 30"><path d="M0 15h120M106 4l14 11-14 11" stroke="#9b9bd0" stroke-width="2.5" fill="none"/></svg>
<p class="abs step-text" style="left:110px">We Boost Foot Traffic To Your Open House Using Proven Marketing Channels, Social Feed Ads, SMS Notifications, Voice Broadcasts and Email Notifications</p>
<p class="abs step-text" style="left:470px">We Place Open House Signs Strategically In The Surrounding Area</p>
<p class="abs step-text" style="left:830px">We Pick Up The Signs Once Your Open House Ends</p>

<section class="block packages">
  <h2 class="abs section-title">PACKAGES</h2>
  <div class="abs pkg" style="left:76px"><div class="badge"><span>5 SIGNS</span><b>$49</b></div><p>Place signs strategically in best areas according to where the open house is located</p><p>Pick Up the signs after the open house</p><p>Store custom signs for you. If needed</p><div class="buy">BUY NOW</div><p class="note">Sign Up For A Subscription To Receive Our Marketing Components For FREE</p></div>
  <div class="abs pkg" style="left:288px"><div class="badge"><span>10 SIGNS</span><b>$59</b></div><p>Place signs strategically in best areas according to where the open house is located</p><p>Pick Up the signs after the open house</p><p>Store custom signs for you. If needed</p><div class="buy">BUY NOW</div><p class="note">Sign Up For A Subscription To Receive Our Marketing Components For FREE</p></div>
  <div class="abs pkg featured" style="left:500px"><div class="badge"><span>15 SIGNS</span><b>$69</b></div><p>Place signs strategically in best areas according to where the open house is located</p><p>Pick Up the signs after the open house</p><p>Store custom signs for you. If needed</p><div class="buy">BUY NOW</div><p class="note">Sign Up For A Subscription To Receive Our Marketing Components For FREE</p></div>
  <div class="abs pkg" style="left:712px"><div class="badge"><span>20 SIGNS</span><b>$79</b></div><p>Place signs strategically in best areas according to where the open house is located</p><p>Pick Up the signs after the open house</p><p>Store custom signs for you. If needed</p><div class="buy">BUY NOW</div><p class="note">Sign Up For A Subscription To Receive Our Marketing Components For FREE</p></div>
  <div class="abs pkg" style="left:924px"><div class="badge"><span>25+ SIGNS</span></div><div class="flag">Click Buy Now To Create Custom Pkg</div><p>Place signs strategically in best areas according to where the open house is located</p><p>Pick Up the signs after the open house</p><p>Store custom signs for you. If needed</p><div class="buy">BUY NOW</div><p class="note">Sign Up For A Subscription To Receive Our Marketing Components For FREE</p></div>
</section>

<section class="block services">
  <h2>SERVICES-SIGN UP FOR A SUBSCRIPTION AND GET THESE MARKETING SERVICES FOR FREE</h2>
  <div class="abs service" style="left:75px">
    <svg width="40" height="44" viewBox="0 0 40 44"><rect x="8" y="2" width="24" height="40" rx="3" fill="none" stroke="#fff" stroke-width="3"/><rect x="20" y="8" width="18" height="12" rx="2" fill="#fff"/></svg>
    <h3>SMS</h3><p>Send sms blast to your neighborhood informing them your home is for sale and if they know anyone looking to send them over</p></div>
  <div class="abs service" style="left:342px">
    <svg width="50" height="40" viewBox="0 0 50 40"><rect x="1" y="4" width="48" height="34" rx="3" fill="#fff"/><path d="M3 7l22 17L47 7" stroke="#2f2f2f" stroke-width="3" fill="none"/></svg>
    <h3>EMAIL</h3><p>Send email blast to your neighborhood informing them your home is for sale and if they know anyone looking to send them over</p></div>
  <div class="abs service" style="left:615px">
    <svg width="42" height="42" viewBox="0 0 42 42"><rect x="1" y="1" width="40" height="40" rx="5" fill="#fff"/></svg>
    <h3>SOCIAL AD</h3><p>Newsfeed ads to people in your open house area</p></div>
  <div class="abs service" style="left:885px">
    <svg width="46" height="42" viewBox="0 0 46 42"><path d="M23 2L2 21h6v19h11V28h8v12h11V21h6z" fill="#fff"/></svg>
    <h3>VB</h3><p>Send VB blast to your neighborhood informing them your home is for sale and if they know anyone looking to send them over</p></div>
</section>

<h2 class="abs section-title area-title" style="color:var(--ink)">SERVICE AREA</h2>
<section class="block area">
  <h2>ENTER YOUR OPEN HOUSE ADDRESS TO SEE IF WE SERVICE IT.</h2>
  <div class="loc">Enter your location
    <svg style="position:absolute;right:12px;top:11px" width="12" height="16" viewBox="0 0 12 16"><path d="M6 0a6 6 0 00-6 6c0 4.5 6 10 6 10s6-5.5 6-10a6 6 0 00-6-6z" fill="#333"/><circle cx="6" cy="6" r="2.2" fill="#fff"/></svg></div>
  <div class="map" role="img" aria-label="Road map of the coastal service region"></div>
</section>

<h2 class="abs section-title faq-title">FAQ</h2>
<div class="abs faq-item" style="top:2955px">
  <div class="q">Lorem Ipsum is simply dummy text of the printing?<svg width="18" height="12" viewBox="0 0 18 12"><path d="M2 2l7 7 7-7" stroke="#444" stroke-width="2.5" fill="none"/></svg></div>
  <div class="a">Lorem ipsum dolor sit amet, consectetur adipiscing elit, sed do eiusmod tempor incididunt ut labore et dolore magna aliqua. Ut enim ad minim veniam, quis nostrud exercitation ullamco laboris nisi ut aliquip ex ea commodo consequat. Duis aute irure dolor in reprehenderit in voluptate velit esse cillum dolore eu fugiat nulla pariatur.</div>
</div>
<div class="abs faq-item" style="top:3150px"><div class="q">Lorem Ipsum is simply dummy text of the printing?<svg width="12" height="18" viewBox="0 0 12 18"><path d="M2 2l7 7-7 7" stroke="#444" stroke-width="2.5" fill="none"/></svg></div></div>
<div class="abs faq-item" style="top:3225px"><div class="q">Lorem Ipsum is simply dummy text of the printing?<svg width="12" height="18" viewBox="0 0 12 18"><path d="M2 2l7 7-7 7" stroke="#444" stroke-width="2.5" fill="none"/></svg></div></div>
<div class="abs faq-item" style="top:3300px"><div class="q">Lorem Ipsum is simply dummy text of the printing?<svg width="12" height="18" viewBox="0 0 12 18"><path d="M2 2l7 7-7 7" stroke="#444" stroke-width="2.5" fill="none"/></svg></div></div>

<section class="block testimonial">
  <h2>TESTIMONIAL</h2>
  <div class="quote-card">
    <div class="avatar" role="img" aria-label="Portrait photo of the client"></div>
    <p>"Suspendisse et quis. Ante vel feugiat. Urna odio tristique. Amet vel semper. Turpis hac in mattis quam placerat tincidunt magna aliquet"</p>
    <b>Lorna</b><small>Freelancer, Belgium</small>
  </div>
  <div class="dots"><i></i><i></i><i></i><i></i></div>
</section>

<h2 class="abs section-title contact-title">CONTACT US RIGHT NOW</h2>
<div class="field" style="left:250px;top:4018px;width:338px;height:40px">NAME</div>
<div class="field" style="left:612px;top:4018px;width:338px;height:40px">EMAIL</div>
<div class="field" style="left:250px;top:4075px;width:700px;height:40px">CELL PHONE</div>
<div class="field" style="left:250px;top:4132px;width:700px;height:90px">MESSAGE</div>
<div class="abs submit">SUBMIT</div>
<div class="abs newsletter"><span>Subscribe Our Newsletter</span></div>

<footer class="block site-footer">
  <div class="abs brand"><span class="brand-mark"></span><span class="brand-name">TallyPorchHelpers.net</span></div>
  <p class="tag">Owned and operated by a highly experienced and skilled Promoter, An Expert Marketer and a Savvy Realtor we help agents leverage their time and skills to increase production at an affordable price with impeccable support!</p>
  <div class="foot-nav"><span>HOW IT WORKS</span><span>SERVICE AREA</span><span>PRICING</span><span>ABOUT US</span><span>FAQ</span></div>
  <p class="copy">Copyright © 2018, Company Name. All Right Reserved</p>
  <div class="social"><i></i><i></i><i></i><i></i><i></i></div>
</footer>

</body>
</html>
```